Poster & Banner for Outback tour company

Poster needed for tour company in the Australian outback. We will need it in an A2 format and if possible a larger banner format as Well please. It needs the Galah Tours logo but also the other logos (less obvious). It also needs to feature the WanderRate logo (uploaded).

The poster needs a list of the tours we offer as well as some of the pictures uploaded.

List of tours:

- Premium Tour of the Town and the Breakaways $99
- Coober Pedy Highlights Tour $85
- Sunset Breakaways Tour $60
- Underground Noodling Tour $50

Industry/Entity Type

Tour Company

Font styles to use
Serif

Colors

Designer to choose colors to be used in the design.

Requirements
Must have
• Galah Tours logo/List of tours/

```html
<!DOCTYPE html>
<html lang="en">
<head>
<meta charset="utf-8">
<title>Galah Tours – List of Tours</title>
<link rel="stylesheet" href="https://fonts.googleapis.com/css2?family=Poppins:wght@400;600;800&family=Montserrat:wght@400;500&display=swap">
<style>
  :root{
    --sky:#4f78c4;
    --sky-deep:#3f5fb0;
    --earth:#b4482a;
    --earth-dark:#5b2116;
    --night:#241712;
    --title-red:#b3181f;
    --title-brown:#3a2418;
    --accent:#f28a1b;
    --price-blue:#3a7c97;
    --price-red:#a8171d;
    --ribbon-cream:#f1ede5;
    --ribbon-grey:#a9a6a1;
    --white:#ffffff;
    --ink:#2d2d2d;
  }
  *{box-sizing:border-box;margin:0;padding:0}
  html,body{width:1200px;height:2741px;overflow:hidden;background:#ffffff}
  .poster{
    position:absolute;left:50px;top:592px;width:1100px;height:1556px;overflow:hidden;
    font-family:"Poppins",sans-serif;color:var(--white);
  }
  .poster-backdrop{
    position:absolute;inset:0;
    background:linear-gradient(180deg,var(--sky-deep) 0%,var(--sky) 20%,#7d9ac4 33%,#d79a5a 40%,var(--earth) 46%,#8a3420 62%,var(--earth-dark) 78%,var(--night) 100%);
  }
  .brand{position:absolute;left:0;right:0;top:52px;text-align:center;font-family:"Poppins",sans-serif;font-weight:600;color:var(--white)}
  .brand-mark{display:inline-block;width:58px;height:58px;background:var(--accent);border-radius:6px;margin-bottom:14px}
  .brand-name{font-size:52px;line-height:1;letter-spacing:1px;text-transform:uppercase}
  .brand-place{font-size:32px;letter-spacing:22px;margin-top:6px;padding-left:22px}
  .headline{position:absolute;left:0;top:290px;width:1100px;height:180px;font-family:"Poppins",sans-serif;font-weight:800;text-transform:uppercase}
  .headline span{position:absolute;line-height:1}
  .headline .red{color:var(--title-red)}
  .headline .brown{color:var(--title-brown)}
  .ribbon{position:absolute;left:373px;top:488px;width:356px;height:76px}
  .ribbon-label{position:absolute;left:0;right:0;top:10px;text-align:center;font-weight:600;font-size:34px;color:var(--ink);letter-spacing:0.5px}
  .tour-list{position:absolute;left:0;top:579px;width:1100px;list-style:none}
  .tour{position:absolute;left:0;width:1100px;height:136px}
  .tour-photo{
    position:absolute;left:88px;top:0;width:306px;height:136px;border-radius:34px;
    border:4px solid var(--white);outline:4px solid var(--accent);
  }
  .tour-info{position:absolute;left:451px;top:0;height:136px;display:flex;flex-direction:column;justify-content:center;text-transform:uppercase}
  .tour-pre,.tour-sub{font-family:"Montserrat",sans-serif;font-weight:500;font-size:25px;line-height:1.3}
  .tour-title{font-weight:800;font-size:38px;line-height:1.05;color:var(--accent);letter-spacing:0.5px}
  .price{
    position:absolute;top:24px;width:160px;height:88px;display:flex;align-items:center;justify-content:center;
    font-weight:800;font-size:60px;color:var(--white);
    clip-path:polygon(6% 8%,94% 0,100% 50%,94% 100%,6% 94%,0 50%);
  }
  .price.blue{background:var(--price-blue)}
  .price.red{background:var(--price-red)}
  .partners{position:absolute;left:95px;top:1226px;width:922px;height:119px}
  .partner-row{position:absolute;left:0;right:0;top:0;height:119px;display:flex;align-items:center;justify-content:center;gap:30px}
  .badge{width:80px;height:96px;background:#2fbf7a}
  .partner{font-family:"Poppins",sans-serif;font-weight:600;font-size:24px;color:var(--ink);line-height:1.05;text-align:center}
  .divider{width:2px;height:70px;background:var(--ink)}
  .website{position:absolute;left:91px;top:1422px;font-weight:600;font-size:41px;color:var(--accent);letter-spacing:0.5px}
</style>
</head>
<body>
<main class="poster">
  <div class="poster-backdrop" role="img" aria-label="Outback landscape: blue sky over white and ochre breakaway hills and red desert plain, darkening to night at the foot"></div>

  <header class="brand">
    <span class="brand-mark"></span>
    <div class="brand-name">Galah Tours</div>
    <div class="brand-place">AUSTRALIA</div>
  </header>

  <h1 class="headline" aria-label="List of Tours">
    <span class="red" style="left:52px;top:58px;font-size:120px">L</span>
    <span class="red" style="left:130px;top:20px;font-size:120px">I</span>
    <span class="red" style="left:170px;top:42px;font-size:120px">S</span>
    <span class="red" style="left:250px;top:58px;font-size:120px">T</span>
    <span class="brown" style="left:402px;top:68px;font-size:125px">O</span>
    <span class="brown" style="left:498px;top:52px;font-size:120px">F</span>
    <span class="red" style="left:628px;top:0;font-size:155px">T</span>
    <span class="red" style="left:690px;top:66px;font-size:130px">O</span>
    <span class="red" style="left:790px;top:40px;font-size:120px">U</span>
    <span class="red" style="left:882px;top:44px;font-size:120px">R</span>
    <span class="red" style="left:972px;top:70px;font-size:120px">S</span>
  </h1>

  <div class="ribbon">
    <svg width="356" height="76" viewBox="0 0 356 76" aria-hidden="true">
      <polygon points="0,30 60,30 60,76 10,76 26,53" fill="var(--ribbon-grey)"/>
      <polygon points="356,30 296,30 296,76 346,76 330,53" fill="var(--ribbon-grey)"/>
      <rect x="50" y="4" width="256" height="56" fill="var(--ribbon-cream)"/>
    </svg>
    <div class="ribbon-label">WE OFFER</div>
  </div>

  <ul class="tour-list">
    <li class="tour" style="top:0">
      <div class="tour-photo" role="img" aria-label="Underground church with stained-glass windows" style="background:linear-gradient(135deg,#7a3a22,#c4703c 50%,#5a2716)"></div>
      <div class="tour-info">
        <span class="tour-pre">Premium tour of the</span>
        <span class="tour-title">Town and<br>the Breakaways</span>
      </div>
      <span class="price blue" style="left:852px">$99</span>
    </li>
    <li class="tour" style="top:157px">
      <div class="tour-photo" role="img" aria-label="Breakaways hills under a blue sky" style="background:linear-gradient(180deg,#4f86cf 0%,#8ab3e2 45%,#e6d2a6 58%,#c2582c 80%,#9b3a20)"></div>
      <div class="tour-info">
        <span class="tour-title">Sunset<br>Breakaways</span>
        <span class="tour-sub">Tour</span>
      </div>
      <span class="price blue" style="left:846px">$60</span>
    </li>
    <li class="tour" style="top:310px">
      <div class="tour-photo" role="img" aria-label="Tour bus parked beside a sandstone dugout" style="background:linear-gradient(180deg,#c98a5c,#a45b36 60%,#7b3d22)"></div>
      <div class="tour-info">
        <span class="tour-title">Coober Pedy</span>
        <span class="tour-sub">Highlights</span>
        <span class="tour-sub">Tour</span>
      </div>
      <span class="price red" style="left:832px">$85</span>
    </li>
    <li class="tour" style="top:464px">
      <div class="tour-photo" role="img" aria-label="Striped desert hills beneath a wide blue sky" style="background:linear-gradient(180deg,#3f78c6 0%,#8fb4e0 42%,#d6b487 58%,#a85a30 80%,#6f3720)"></div>
      <div class="tour-info">
        <span class="tour-title">Underground</span>
        <span class="tour-sub">Noodling</span>
        <span class="tour-sub">Tour</span>
      </div>
      <span class="price red" style="left:830px">$50</span>
    </li>
  </ul>

  <section class="partners" aria-label="Partners">
    <svg width="922" height="119" viewBox="0 0 922 119" aria-hidden="true" style="position:absolute;left:0;top:0">
      <polygon points="0,0 922,0 890,60 922,119 0,119 32,60" fill="var(--white)"/>
    </svg>
    <div class="partner-row">
      <div class="badge" role="img" aria-label="WanderRate award badge"></div>
      <span class="partner">Clay House<br>Inn</span>
      <span class="partner">Ridgeline<br>Outback Stay</span>
      <span class="divider"></span>
      <span class="partner">Dune<br>Parks</span>
      <span class="divider"></span>
      <span class="partner">Saltbush<br>Villages</span>
    </div>
  </section>

  <p class="website">WWW.GALAHTOURS.EXAMPLE</p>
</main>
</body>
</html>
```